Private Investigation Business Card Design

I need a business card for a new private investigation company named Brisk Inquiries. I perform mainly surveillance jobs, vehicle repossessions, document serves etc. The final design should aim for a professional look. The logo has a magnifying glass with stick man arms and legs and is in a running action to show the "Brisk" aspect of the name. If the colour scheme could remain the same as the website www.briskinquiries-demo.com.au with silvers,blacks and a couple electric blue highlights.
Industry/Entity Type
Business
Contact Information for Business Card
Morgan Kellaway
Brisk Inquiries
0487316204
PO Box 58, Carnwell NSW 2291
info@briskinquiries-demo.com.au
www.briskinquiries-demo.com.au
Look and feel

```html
<!DOCTYPE html>
<html lang="en">
<head>
<meta charset="utf-8">
<title>Brisk Inquiries – Business Card</title>
<link rel="stylesheet" href="https://fonts.googleapis.com/css2?family=Lato:wght@400;700&display=swap">
<style>
  :root {
    --backdrop: #e4e4e4;
    --card-white: #fbfbfb;
    --card-dark: #3b3c3e;
    --band-black: #1d1d1f;
    --ink: #4a4a4a;
    --ink-strong: #575757;
    --brand-silver: #6e6e70;
    --brand-silver-light: #a9a9ab;
    --divider: #5a5a5a;
  }
  * { margin: 0; padding: 0; box-sizing: border-box; }
  html, body {
    width: 1200px; height: 720px; overflow: hidden;
    background: var(--backdrop);
    font-family: "Lato", Arial, sans-serif;
  }
  .canvas { position: relative; width: 1200px; height: 720px; }

  .card {
    position: absolute; top: 241px; width: 420px; height: 240px;
    border-radius: 6px; overflow: hidden;
  }
  .card--front { left: 147px; background: var(--card-white); }
  .card--back { left: 633px; background: var(--card-dark); }

  .brand {
    position: absolute; display: flex; align-items: center; gap: 8px;
    font-weight: 700; white-space: nowrap; letter-spacing: 0.2px;
  }
  .card--front .brand { left: 28px; top: 106px; font-size: 20px; color: var(--brand-silver); }
  .brand__dot {
    display: inline-block; width: 14px; height: 14px; border-radius: 50%;
    background: currentColor;
  }
  .card--back .brand {
    left: 0; right: 0; top: 100px; justify-content: center;
    font-size: 34px; color: var(--brand-silver-light);
  }
  .card--back .brand__dot { width: 22px; height: 22px; }

  .divider {
    position: absolute; left: 208px; top: 55px; width: 2px; height: 136px;
    background: var(--divider);
  }
  .details { position: absolute; left: 215px; top: 56px; color: var(--ink); }
  .details__name { font-size: 17px; font-weight: 700; color: var(--ink-strong); line-height: 20px; }
  .details__role { font-size: 12px; line-height: 16px; }
  .details__address { margin-top: 18px; font-size: 12px; line-height: 14px; }
  .details__contacts { margin-top: 14px; list-style: none; font-size: 11.5px; line-height: 13px; }
  .details__contacts li { display: flex; align-items: center; gap: 5px; }
  .details__contacts svg { width: 11px; height: 10px; flex: none; }

  .base-band {
    position: absolute; left: 0; bottom: 0; width: 100%; height: 15px;
    background: var(--band-black);
  }
  .base-band__slash { position: absolute; left: 284px; bottom: 0; width: 14px; height: 15px; }
</style>
</head>
<body>
<main class="canvas">

  <section class="card card--front" aria-label="Business card front">
    <div class="brand"><span>Brisk Inquiries</span><span class="brand__dot"></span></div>
    <div class="divider"></div>
    <div class="details">
      <p class="details__name">Morgan Kellaway</p>
      <p class="details__role">Director</p>
      <p class="details__address">PO Box 58<br>Carnwell NSW 2291</p>
      <ul class="details__contacts">
        <li>
          <svg viewBox="0 0 11 10" aria-hidden="true"><path d="M1 4 Q1 1 5.5 1 Q10 1 10 4 L8 4 L7.5 3 L3.5 3 L3 4 Z M3 5 L8 5 L9.5 9 L1.5 9 Z" fill="#4a4a4a"/></svg>
          0487316204
        </li>
        <li>
          <svg viewBox="0 0 11 10" aria-hidden="true"><rect x="0.5" y="1.5" width="10" height="7" fill="#4a4a4a"/><path d="M0.8 2 L5.5 5.5 L10.2 2" stroke="#fbfbfb" stroke-width="1" fill="none"/></svg>
          info@briskinquiries-demo.com.au
        </li>
        <li>
          <svg viewBox="0 0 11 10" aria-hidden="true"><rect x="0.8" y="0.8" width="9.4" height="6.4" fill="none" stroke="#4a4a4a" stroke-width="1.2"/><rect x="3.5" y="8" width="4" height="1.4" fill="#4a4a4a"/></svg>
          www.briskinquiries-demo.com.au
        </li>
      </ul>
    </div>
    <div class="base-band">
      <svg class="base-band__slash" viewBox="0 0 14 15" aria-hidden="true"><line x1="2" y1="15" x2="12" y2="0" stroke="#f2f2f2" stroke-width="1.6"/></svg>
    </div>
  </section>

  <section class="card card--back" aria-label="Business card back">
    <div class="brand"><span>Brisk Inquiries</span><span class="brand__dot"></span></div>
  </section>

</main>
</body>
</html>
```